Vardem Web, LLC. is the name of the company that will be an Internet startup working in E-commerce and

We are a new company and going to start the business by hiring people we need. We are on “Hiring Now…” status right now which we like to be displayed on the website homepage.
The website should allow us to start the hiring process with letting people see and apply for jobs posted on the website.

the company logo is attached.

Target Market(s)

Tech Job Seekers, Programmers, iOS and Android Developers, Software engineers, Graphic designers, QA engineers, Customer Service Reps,...

Industry/Entity Type

Internet

Number of Pages Required

5+ page

Font styles to use
Serif
Sans Serif

Colors

Designer to choose colors to be used in the design.

Requirements
Must have
• We need a system to help job seekers to upload the resume and cover letter and fill the required forms and answer some questions on a form designed to evaluate the job seekers and let them know if they fit in the position and should apply for it.
• We also want job seekers to do a Pre-Employment Tests including Aptitude, Personality, and Skills after they qualified for a job which links our website to web-based pre-employment testing services websites like (Talvexa, Plivmark, Quorvane & Associates, Dunholt Assessment, …)

```html
<!DOCTYPE html>
<html lang="en">
<head>
<meta charset="utf-8">
<title>Vardem Web – Careers</title>
<link href="https://fonts.googleapis.com/css2?family=Nunito:wght@400;600;700&family=Open+Sans:wght@400;600&display=swap" rel="stylesheet">
<style>
:root{
  --blue:#3a9ad1;
  --blue-dark:#2a86bf;
  --orange:#f15a24;
  --ink:#222;
  --text:#555;
  --muted:#8a8a8a;
  --light:#f3f3f3;
  --footer:#1b1b1b;
  --line:#3a3a3a;
  --white:#fff;
}
*{box-sizing:border-box;margin:0;padding:0}
html,body{width:1200px;height:3175px;overflow:hidden}
body{font-family:"Open Sans",Arial,sans-serif;color:var(--text);background:var(--white);position:relative}
.abs{position:absolute}
a{color:inherit;text-decoration:none}

/* header */
.topbar{position:absolute;left:0;top:0;width:1200px;height:105px}
.social{position:absolute;left:88px;top:36px;display:flex;gap:10px}
.social span{width:18px;height:18px;border-radius:3px;background:var(--blue)}
.social span:first-child{background:#3b5ba0}
.social span:last-child{background:#d9473b}
.brand{position:absolute;left:0;width:1200px;top:28px;text-align:center;font-family:"Nunito",sans-serif;font-weight:700;font-size:34px;color:var(--blue);display:flex;justify-content:center;align-items:center;gap:10px}
.brand i{display:inline-block;width:14px;height:14px;border-radius:50%;background:var(--orange)}
.btn-outline,.btn-fill{position:absolute;top:32px;height:34px;border-radius:17px;font-size:15px;display:flex;align-items:center;justify-content:center}
.btn-outline{left:845px;width:140px;border:1.5px solid var(--blue);color:var(--blue)}
.btn-fill{left:992px;width:118px;background:var(--orange);color:var(--white)}

.nav{position:absolute;left:0;top:105px;width:1200px;height:55px;background:linear-gradient(#4aa8dc,var(--blue-dark));display:flex;padding-left:88px}
.nav a{color:var(--white);font-family:"Nunito",sans-serif;font-size:17px;display:flex;align-items:center;padding:0 27px}
.nav a.active{background:#1f1f1f;width:118px;justify-content:center}

/* hero */
.hero{position:absolute;left:0;top:160px;width:1200px;height:547px;background:linear-gradient(90deg,#ececec 0%,#e2e2e2 40%,#8d8f93 60%,#3a3d44 80%,#6c6f75 100%)}
.hero-title{position:absolute;left:88px;top:178px;font-size:50px;font-weight:600;color:var(--blue);letter-spacing:1px}
.hero-sub{position:absolute;left:90px;top:233px;font-size:27px;color:#333}
.hero-arrows{position:absolute;left:88px;top:288px;display:flex;gap:6px}
.hero-arrows span{width:20px;height:20px;border-radius:50%;background:#777;display:flex;align-items:center;justify-content:center}
.search{position:absolute;left:88px;top:449px;width:1112px;height:98px;background:rgba(40,40,40,.85);display:flex;align-items:center;padding-left:24px;gap:16px}
.field{height:42px;background:var(--white);font-size:12px;color:#555;display:flex;align-items:center;padding:0 12px;justify-content:space-between}
.field.kw{width:304px}
.field.sel{width:240px}
.field.sel::after{content:"";border:5px solid transparent;border-top-color:#333;margin-top:5px}
.btn-find{margin-left:10px;width:140px;height:42px;background:#5bc1d8;color:var(--white);font-size:16px;display:flex;align-items:center;justify-content:center}

/* section headings */
.h2{position:absolute;left:0;width:1200px;text-align:center;font-family:"Nunito",sans-serif;font-size:32px;color:var(--ink);letter-spacing:.5px}

/* categories */
.cat{position:absolute;top:902px;width:250px;text-align:center}
.cat .ring{width:106px;height:106px;border-radius:50%;border:1.5px solid #888;margin:0 auto;display:flex;align-items:center;justify-content:center}
.cat h3{font-family:"Nunito",sans-serif;font-weight:400;font-size:17px;color:var(--ink);margin-top:26px}
.cat p{font-size:12px;line-height:20px;color:var(--muted);margin-top:14px;padding:0 8px}
.chev{position:absolute;top:980px}

/* perfect job */
.profile{position:absolute;left:0;top:1220px;width:1200px;height:408px;background:linear-gradient(90deg,#c9d7e6 0%,#e5edf5 40%,#f5f8fb 60%,#fbfcfd 100%)}
.profile-img{position:absolute;left:0;top:0;width:540px;height:408px;background:radial-gradient(circle at 45% 45%,#d8e4ef 0%,#b9cde1 50%,#9fb8d2 100%)}
.profile h2{position:absolute;left:556px;top:92px;font-family:"Nunito",sans-serif;font-weight:600;font-size:28px;color:var(--ink)}
.ticks{position:absolute;left:556px;top:146px;list-style:none;font-size:14px;line-height:26px;color:#444}
.ticks li{display:flex;align-items:center;gap:10px}
.profile p{position:absolute;left:556px;top:228px;width:545px;font-size:14px;line-height:26px;color:#444}
.btn-test{position:absolute;left:556px;top:295px;width:190px;height:32px;border-radius:16px;background:var(--orange);color:var(--white);font-size:14px;font-weight:600;display:flex;align-items:center;justify-content:center}

/* featured jobs */
.job{position:absolute;width:500px;height:154px;background:var(--white);box-shadow:0 2px 6px rgba(0,0,0,.18);display:flex}
.job .thumb{width:164px;height:154px;background:linear-gradient(135deg,#9fb0c2,#4f5d70)}
.job .body{padding:18px 20px 0 25px;flex:1}
.job h3{font-size:14px;font-weight:600;color:var(--ink)}
.job p{font-size:12px;line-height:21px;color:var(--text);margin-top:12px;text-align:justify}
.more{font-size:12px;color:var(--orange);display:block;margin-top:8px}
.dots{position:absolute;top:2200px;left:579px;display:flex;gap:8px}
.dots span{width:9px;height:9px;border-radius:50%;background:#333}
.dots span:first-child{background:var(--blue)}

/* news */
.news{position:absolute;left:0;top:2316px;width:1200px;height:529px;background:var(--light)}
.post{position:absolute;top:147px;width:313px}
.post .thumb{height:174px;background:linear-gradient(135deg,#d6dbe0,#7e8791)}
.meta{display:flex;margin-top:12px;font-size:12px;color:var(--white)}
.meta .date{background:var(--blue);width:64px;height:25px;display:flex;align-items:center;justify-content:center}
.meta .cm{background:#222;width:36px;height:25px;display:flex;align-items:center;justify-content:center;gap:3px}
.post h3{font-family:"Nunito",sans-serif;font-weight:400;font-size:16px;color:var(--ink);margin-top:14px}
.post p{font-size:13px;line-height:20px;color:var(--text);margin-top:8px}

/* footer */
.footer{position:absolute;left:0;top:2845px;width:1200px;height:330px;background:var(--footer);color:#ddd}
.f-brand{position:absolute;left:88px;top:140px;font-family:"Nunito",sans-serif;font-weight:700;font-size:26px;color:#e6e6e6;display:flex;align-items:center;gap:8px}
.f-brand i{width:12px;height:12px;border-radius:50%;background:#e6e6e6;display:inline-block}
.f-col{position:absolute;top:72px}
.f-col h4{font-family:"Nunito",sans-serif;font-weight:400;font-size:17px;color:#eee;margin-bottom:14px}
.f-col li{list-style:none;font-size:12px;line-height:24px;color:#ddd}
.f-col li::before{content:"›";margin-right:8px}
.f-col.contact li::before{content:none}
.f-col.contact li{display:flex;align-items:center;gap:8px;line-height:30px}
.f-rule{position:absolute;left:78px;top:228px;width:1022px;height:1px;background:var(--line)}
.copy{position:absolute;left:88px;top:267px;font-size:12px;color:#ddd}
.f-social{position:absolute;left:896px;top:263px;display:flex;gap:8px}
.f-social span{width:24px;height:24px;border-radius:50%;border:1px solid #bbb}
</style>
</head>
<body>

<header class="topbar">
  <div class="social"><span></span><span></span><span></span><span></span></div>
  <div class="brand"><i></i>Vardem Web</div>
  <a class="btn-outline" href="#">Upload Resume</a>
  <a class="btn-fill" href="#">Cover Letter</a>
</header>

<nav class="nav">
  <a class="active" href="#">Home</a>
  <a href="#">For companies</a>
  <a href="#">For candidates</a>
  <a href="#">Job portal</a>
  <a href="#">Support</a>
  <a href="#">News</a>
  <a href="#">Contact</a>
</nav>

<section class="hero" role="img" aria-label="Business people shaking hands in a bright office">
  <div class="hero-title">HIRING NOW...</div>
  <div class="hero-sub">Neque porro quisquam est</div>
  <div class="hero-arrows">
    <span><svg width="8" height="8" viewBox="0 0 8 8"><path d="M5 1 2 4l3 3" stroke="#fff" fill="none" stroke-width="1.5"/></svg></span>
    <span><svg width="8" height="8" viewBox="0 0 8 8"><path d="M3 1l3 3-3 3" stroke="#fff" fill="none" stroke-width="1.5"/></svg></span>
  </div>
  <form class="search">
    <div class="field kw">Job Title, Keywords, Company Name</div>
    <div class="field sel">All Location</div>
    <div class="field sel">Any category</div>
    <div class="btn-find">FIND JOBS</div>
  </form>
</section>

<h2 class="h2" style="top:805px">POPULAR CATEGORIES</h2>
<svg class="chev" style="left:52px" width="16" height="36" viewBox="0 0 16 36"><path d="M14 2 2 18l12 16" stroke="#999" fill="none" stroke-width="1.5"/></svg>
<svg class="chev" style="left:1134px" width="16" height="36" viewBox="0 0 16 36"><path d="M2 2l12 16L2 34" stroke="#999" fill="none" stroke-width="1.5"/></svg>

<div class="cat" style="left:76px">
  <div class="ring"><svg width="44" height="36" viewBox="0 0 44 36"><path d="M2 2v32h40" stroke="#2a86bf" fill="none" stroke-width="3"/><path d="M8 26l10-10 7 7 13-13" stroke="#2a86bf" fill="none" stroke-width="3"/><path d="M31 9h8v8" stroke="#2a86bf" fill="none" stroke-width="3"/></svg></div>
  <h3>Accountance</h3>
  <p>It has survived not only five centu-ries, but also the leap into electronic typesetting, remaining</p>
</div>
<div class="cat" style="left:345px">
  <div class="ring"><svg width="42" height="40" viewBox="0 0 42 40"><path d="M21 2 2 12h38z" fill="#2a86bf"/><rect x="6" y="15" width="5" height="16" fill="#2a86bf"/><rect x="14.5" y="15" width="5" height="16" fill="#2a86bf"/><rect x="23" y="15" width="5" height="16" fill="#2a86bf"/><rect x="31.5" y="15" width="5" height="16" fill="#2a86bf"/><rect x="2" y="33" width="38" height="5" fill="#2a86bf"/></svg></div>
  <h3>Banking</h3>
  <p>It has survived not only five centu-ries, but also the leap into electronic typesetting, remaining</p>
</div>
<div class="cat" style="left:615px">
  <div class="ring"><svg width="36" height="36" viewBox="0 0 36 36"><path d="M25 3l8 8L13 31l-10 3 3-10z" fill="#2a86bf"/><path d="M22 6l8 8" stroke="#fff" stroke-width="2"/></svg></div>
  <h3>Design &amp; Art</h3>
  <p>It has survived not only five centu-ries, but also the leap into electronic typesetting, remaining</p>
</div>
<div class="cat" style="left:878px">
  <div class="ring"><svg width="42" height="38" viewBox="0 0 42 38"><rect x="2" y="2" width="38" height="26" rx="2" fill="none" stroke="#2a86bf" stroke-width="3.5"/><path d="M16 28v6h10v-6M11 36h20" stroke="#2a86bf" fill="none" stroke-width="3.5"/></svg></div>
  <h3>IT Engineer</h3>
  <p>It has survived not only five centu-ries, but also the leap into electron-ic typesetting, remaining</p>
</div>

<section class="profile">
  <div class="profile-img" role="img" aria-label="Hand pointing at a network of people icons with one highlighted in a red circle"></div>
  <h2>FIND THE PERFECT JOB AS YOUR PROFILE</h2>
  <ul class="ticks">
    <li><svg width="13" height="13" viewBox="0 0 13 13"><rect x=".5" y=".5" width="12" height="12" fill="none" stroke="#2a86bf"/><path d="M3 6.5l2.5 2.5L10 4" stroke="#2a86bf" fill="none" stroke-width="1.6"/></svg>Condimentum eros pretium nam vel magnas nec diam.</li>
    <li><svg width="13" height="13" viewBox="0 0 13 13"><rect x=".5" y=".5" width="12" height="12" fill="none" stroke="#2a86bf"/><path d="M3 6.5l2.5 2.5L10 4" stroke="#2a86bf" fill="none" stroke-width="1.6"/></svg>Diam commodo viverra eget leo curabitur diam consequat</li>
    <li><svg width="13" height="13" viewBox="0 0 13 13"><rect x=".5" y=".5" width="12" height="12" fill="none" stroke="#2a86bf"/><path d="M3 6.5l2.5 2.5L10 4" stroke="#2a86bf" fill="none" stroke-width="1.6"/></svg>Nam luctus venenatis mauris et luctus sem lacinia et.</li>
  </ul>
  <p>It is a long established fact that a reader will be distracted by the readable content of a page when looking at its layout. The point of using Lorem Ipsum is that</p>
  <a class="btn-test" href="#">Pre-Employment Tests</a>
</section>

<h2 class="h2" style="top:1748px">MOST AMAZING FEATURED JOB LISTED</h2>

<article class="job" style="left:88px;top:1830px">
  <div class="thumb" role="img" aria-label="Business team in a meeting"></div>
  <div class="body"><h3>Porro quisquam est qui</h3><p>Lorem Ipsum has been the industry's standard dummy text ever since the 1500s, when an unknown printer took a galley of type and scrambled</p><a class="more" href="#">Read More &gt;&gt;</a></div>
</article>
<article class="job" style="left:612px;top:1830px">
  <div class="thumb" role="img" aria-label="Colleagues greeting in an office"></div>
  <div class="body"><h3>Quisquam est qui dolorem</h3><p>Lorem Ipsum has been the industry's standard dummy text ever since the 1500s, when an unknown printer took a galley of type and scrambled</p><a class="more" href="#">Read More &gt;&gt;</a></div>
</article>
<article class="job" style="left:88px;top:2005px">
  <div class="thumb" role="img" aria-label="Job interview at a desk"></div>
  <div class="body"><h3>Ipsum quia dolor sit amet</h3><p>Lorem Ipsum has been the industry's standard dummy text ever since the 1500s, when an unknown printer took a galley of type and scrambled</p><a class="more" href="#">Read More &gt;&gt;</a></div>
</article>
<article class="job" style="left:612px;top:2005px">
  <div class="thumb" role="img" aria-label="Group of professionals in business attire"></div>
  <div class="body"><h3>Dolorem ipsum quia dolor</h3><p>Lorem Ipsum has been the industry's standard dummy text ever since the 1500s, when an unknown printer took a galley of type and scrambled</p><a class="more" href="#">Read More &gt;&gt;</a></div>
</article>
<div class="dots"><span></span><span></span><span></span></div>

<section class="news">
  <h2 class="h2" style="top:64px">LATEST NEWS</h2>
  <article class="post" style="left:95px">
    <div class="thumb" role="img" aria-label="Two businessmen shaking hands"></div>
    <div class="meta"><span class="date">Dec 03</span><span class="cm"><svg width="12" height="10" viewBox="0 0 12 10"><path d="M1 1h10v6H5L2 9V7H1z" fill="none" stroke="#fff"/></svg>0</span></div>
    <h3>Neque porro quisquam dolorem</h3>
    <p>It has survived not only five centuries, but also the leap into electronic typesetting,</p>
    <a class="more" href="#">Read More »</a>
  </article>
  <article class="post" style="left:443px">
    <div class="thumb" role="img" aria-label="Interview across a desk with a laptop"></div>
    <div class="meta"><span class="date">Dec 03</span><span class="cm"><svg width="12" height="10" viewBox="0 0 12 10"><path d="M1 1h10v6H5L2 9V7H1z" fill="none" stroke="#fff"/></svg>0</span></div>
    <h3>Porro quisquam est qui</h3>
    <p>It has survived not only five centuries, but also the leap into electronic typesetting,</p>
    <a class="more" href="#">Read More »</a>
  </article>
  <article class="post" style="left:797px">
    <div class="thumb" role="img" aria-label="Candidate talking with a recruiter by a brick wall"></div>
    <div class="meta"><span class="date">Dec 03</span><span class="cm"><svg width="12" height="10" viewBox="0 0 12 10"><path d="M1 1h10v6H5L2 9V7H1z" fill="none" stroke="#fff"/></svg>0</span></div>
    <h3>Dolorem ipsum quia dolor</h3>
    <p>It has survived not only five centuries, but also the leap into electronic typesetting,</p>
    <a class="more" href="#">Read More »</a>
  </article>
</section>

<footer class="footer">
  <div class="f-brand"><i></i>Vardem Web</div>
  <div class="f-col" style="left:370px"><h4>Links</h4><ul><li>Home</li><li>Services</li><li>Job Listing</li><li>About us</li></ul></div>
  <div class="f-col" style="left:523px"><h4>Information</h4><ul><li>Privacy Policy</li><li>Login</li><li>Advanced Search</li><li>Contact Us</li></ul></div>
  <div class="f-col" style="left:700px"><h4>Quicklink</h4><ul><li>For companies</li><li>For candidates</li><li>Job portal</li><li>Support</li></ul></div>
  <div class="f-col contact" style="left:890px"><h4>Contact</h4><ul>
    <li><svg width="10" height="13" viewBox="0 0 10 13"><path d="M5 0a5 5 0 0 0-5 5c0 4 5 8 5 8s5-4 5-8a5 5 0 0 0-5-5z" fill="#ddd"/><circle cx="5" cy="5" r="1.8" fill="#1b1b1b"/></svg>42 Harlow Lane, Brenmoor, IL 60411</li>
    <li><svg width="12" height="12" viewBox="0 0 12 12"><path d="M2 0l3 3-1.5 2a7 7 0 0 0 3.5 3.5L9 7l3 3-2 2C5 12 0 7 0 2z" fill="#ddd"/></svg>(555) 014-2270</li>
    <li><svg width="13" height="10" viewBox="0 0 13 10"><rect width="13" height="10" fill="#ddd"/><path d="M0 0l6.5 5L13 0" stroke="#1b1b1b" fill="none"/></svg>hello@vardemweb.example</li>
  </ul></div>
  <div class="f-rule"></div>
  <div class="copy">Copyright © 2017. All Rights Reserved</div>
  <div class="f-social"><span></span><span></span><span></span><span></span><span></span><span></span></div>
</footer>

</body>
</html>
```